Company that sells high quality boat cleaning supplies needs new Homepage Design

We need a homepage design for a company that sells high quality boat cleaning and maintanence products. This company is called VPX61. There are 3 primary products; a soap for boats, waterless wash & Wax, and a Ceramic Spray coating and protectant.

Current Website: https://vpx61.com/

Customer Avatar/ Core Message Canvas: https://sheets.tarvolin.net/s/7qWk2Lp9RbXe4TnHy8MfC3uZaD1oJv6GsKxE5iBtN0Ph/view?share=open

Homepage Template: https://sheets.tarvolin.net/d/4Hb8nYc2QwLe6RkT0vMxJ5aPfZ9uGtSoDi3Ck7EyBn1V/view?share=open

There is info on imagery in the homepage template. Where there isn't, appropriate stock imagery is acceptable.

Logo Design and Slogan images: https://vault.tarvolin.net/f/9kLmQ2rTz8WyHn4PcVb6XeJ0gA5sDu7?share=open

Product Images: https://vault.tarvolin.net/f/3pNcR7wYh1KeTm8ZsVa4QbLu6Dj9Fgx?share=open

```html
<!DOCTYPE html>
<html lang="en">
<head>
<meta charset="utf-8">
<title>VPX61 — Stress-Free Boat Care</title>
<link href="https://fonts.googleapis.com/css2?family=Montserrat:wght@400;500;600;700&family=Lato:wght@400;700&display=swap" rel="stylesheet">
<style>
  :root{
    --green:#5d7352;
    --green-deep:#55694b;
    --green-soft:#6a8060;
    --dark:#141414;
    --black:#050505;
    --white:#ffffff;
    --ink:#111111;
    --body:#333333;
    --muted:#eef0ee;
    --band:#f2f2f2;
    --hero-a:#6f7780;
    --hero-b:#a9b2ba;
  }
  *{box-sizing:border-box;margin:0;padding:0}
  html,body{width:1200px;height:4380px;overflow:hidden}
  body{position:relative;background:var(--white);font-family:"Lato",sans-serif;color:var(--ink)}
  .abs{position:absolute}
  .heading{font-family:"Montserrat",sans-serif}

  /* Hero */
  .hero{left:0;top:0;width:1200px;height:685px;overflow:hidden;
    background:linear-gradient(100deg,#4c535a 0%,#6d767e 38%,#9ea8b1 70%,#c5ccd2 100%)}
  .hero-photo{left:0;top:0;width:1200px;height:685px;
    background:radial-gradient(ellipse 380px 420px at 820px 360px,rgba(60,90,130,.55),transparent 70%),
               linear-gradient(0deg,rgba(0,0,0,.25),transparent 45%)}
  .logo{font-family:"Montserrat",sans-serif;font-weight:600;color:var(--white);letter-spacing:-1px}
  .hero .logo{left:110px;top:30px;font-size:48px;line-height:52px}
  .nav a{position:absolute;top:46px;font-family:"Montserrat",sans-serif;font-size:14px;color:var(--white);text-decoration:none}
  .pill{position:absolute;top:31px;height:35px;border-radius:5px;display:flex;align-items:center;gap:8px;
    padding:0 10px;font-family:"Montserrat",sans-serif;font-size:12px;font-weight:600;color:var(--white)}
  .pill .dot{width:20px;height:20px;border-radius:50%;background:var(--white);display:flex;align-items:center;justify-content:center}
  .login{left:894px;width:97px;background:var(--green)}
  .cart{left:1000px;width:83px;border:1px solid rgba(255,255,255,.8);font-weight:500}
  .hero-title{left:110px;top:182px;width:640px;font-size:51px;line-height:59.5px;font-weight:700;color:var(--white)}
  .hero-sub{left:112px;top:438px;font-family:"Montserrat",sans-serif;font-size:15px;color:var(--white)}
  .btn{position:absolute;display:flex;align-items:center;justify-content:center;border-radius:5px;
    font-family:"Montserrat",sans-serif;font-weight:700;font-size:15px;letter-spacing:.2px;text-decoration:none}
  .btn-outline{border:2px solid var(--white);color:var(--white)}
  .btn-green{background:var(--green);color:var(--white);box-shadow:0 3px 8px rgba(0,0,0,.18)}
  .btn-white{background:var(--white);color:var(--green);box-shadow:0 3px 8px rgba(0,0,0,.15)}

  /* Features */
  .feature{position:absolute;top:788px;width:220px;margin-left:-110px;text-align:center}
  .feature .icon{width:76px;height:76px;border-radius:50%;background:#dcdcdc;margin:0 auto;display:flex;align-items:center;justify-content:center}
  .feature .label{margin-top:20px;font-family:"Montserrat",sans-serif;font-weight:600;font-size:21px;line-height:30px;color:var(--ink)}

  /* Product bands */
  .band{left:0;width:1200px;height:500px;overflow:hidden}
  .band-green{background:var(--green)}
  .band-dark{background:var(--dark)}
  .video{position:absolute;width:432px;height:370px}
  .play{position:absolute;left:50%;top:50%;width:62px;height:62px;margin:-31px 0 0 -31px;border-radius:50%;
    background:var(--green);display:flex;align-items:center;justify-content:center}
  .product-title{position:absolute;font-family:"Montserrat",sans-serif;font-weight:700;font-size:35px;line-height:44px;color:var(--white)}

  /* Solution */
  .section-title{width:1200px;left:0;text-align:center;font-family:"Montserrat",sans-serif;font-weight:700}
  .card{position:absolute;width:730px;height:264px;background:var(--white);border-radius:6px;
    box-shadow:0 8px 38px rgba(0,0,0,.10);padding:36px 50px}
  .card h3{font-family:"Montserrat",sans-serif;font-weight:700;font-size:18px;color:var(--ink);margin-bottom:16px}
  .card p{font-size:14px;line-height:30px;color:var(--body)}

  /* Newsletter */
  .newsletter{left:0;top:3548px;width:1200px;height:389px;background:var(--band)}

  /* Footer */
  .footer{left:0;top:3937px;width:1200px;height:443px;background:var(--black);color:var(--white)}
  .footer .logo{left:105px;top:90px;font-size:76px;line-height:80px}
  .social{position:absolute;top:222px;width:26px;height:26px;border-radius:50%;background:var(--green)}
  .fcol{position:absolute;top:100px}
  .fcol h4{font-family:"Montserrat",sans-serif;font-weight:700;font-size:16px;margin-bottom:20px;letter-spacing:.3px}
  .fcol li{list-style:none;font-size:14px;line-height:30px}
  .fcol li::before{content:"«";color:#9a9a9a;margin-right:10px}
  .contact li::before{content:none}
  .contact li{display:flex;gap:14px;align-items:flex-start;line-height:22px;margin-bottom:12px}
  .rule{left:110px;top:335px;width:980px;height:1px;background:#262626}
  .copy{left:0;top:376px;width:1200px;text-align:center;font-size:14px}
</style>
</head>
<body>

<!-- Hero -->
<section class="abs hero">
  <div class="abs hero-photo" role="img" aria-label="Smiling man in a denim jacket steering a boat at the helm, sea in the background"></div>
  <div class="abs logo">VPX61</div>
  <nav class="nav">
    <a style="left:502px">Home</a>
    <a style="left:585px">Blog</a>
    <a style="left:647px">Contact</a>
    <a style="left:740px">Shop VPX61</a>
  </nav>
  <div class="pill login"><span class="dot"><svg width="12" height="12" viewBox="0 0 12 12"><circle cx="6" cy="4" r="2.5" fill="#5d7352"/><path d="M1.5 11c0-2.6 2-4 4.5-4s4.5 1.4 4.5 4z" fill="#5d7352"/></svg></span>LOGIN</div>
  <div class="pill cart"><span class="dot"><svg width="12" height="12" viewBox="0 0 12 12"><path d="M1 2h2l1.3 5.5h5.2L10.8 4H4" stroke="#888" stroke-width="1.3" fill="none"/><circle cx="5" cy="10" r="1" fill="#888"/><circle cx="9" cy="10" r="1" fill="#888"/></svg></span>CART</div>
  <h1 class="abs heading hero-title">Stress-Free Boat Care: VPX61 Takes The Hard Work Out of Cleaning &amp; Detailing</h1>
  <p class="abs hero-sub">ECO Friendly &nbsp;• Simple Application • Advanced Nanotechnologies</p>
  <a class="btn btn-outline" style="left:112px;top:498px;width:158px;height:55px">OUR BLOG</a>
  <a class="btn btn-green" style="left:292px;top:498px;width:158px;height:55px">SHOP VPX61</a>
</section>

<!-- Features -->
<section>
  <div class="feature" style="left:182px"><div class="icon"><svg width="34" height="34" viewBox="0 0 34 34" fill="none" stroke="#666" stroke-width="1.5"><rect x="9" y="5" width="16" height="24" rx="2"/><path d="M13 11h8M13 16h8M13 21h5"/></svg></div><div class="label">SIMPLE<br>APPLICATION</div></div>
  <div class="feature" style="left:367px"><div class="icon"><svg width="38" height="38" viewBox="0 0 38 38" fill="none" stroke="#666" stroke-width="1.5"><circle cx="19" cy="19" r="15"/><circle cx="19" cy="19" r="10"/></svg></div><div class="label">MADE IN<br>THE USA</div></div>
  <div class="feature" style="left:561px"><div class="icon"><svg width="34" height="34" viewBox="0 0 34 34" fill="none" stroke="#666" stroke-width="1.5"><path d="M17 5l5 9h-10z"/><path d="M8 27l5-9 5 9z"/><path d="M26 27l-5-9"/></svg></div><div class="label" style="margin-top:30px">ECO FRIENDLY</div></div>
  <div class="feature" style="left:796px"><div class="icon"><svg width="34" height="34" viewBox="0 0 34 34" fill="none" stroke="#666" stroke-width="1.5"><rect x="6" y="8" width="22" height="18"/><path d="M9 22l6-6 4 3 6-7"/></svg></div><div class="label">DESIGNED FOR<br>ANY &nbsp;CONDITIONS</div></div>
  <div class="feature" style="left:1023px"><div class="icon"><svg width="34" height="34" viewBox="0 0 34 34" fill="none" stroke="#666" stroke-width="1.5"><circle cx="14" cy="14" r="6"/><circle cx="14" cy="14" r="2"/><circle cx="23" cy="22" r="4"/></svg></div><div class="label">WORKS THE<br>FIRST TIME</div></div>
</section>

<!-- Product: Waterless Wash & Wax -->
<section class="abs band band-green" style="top:1061px">
  <svg class="abs" style="left:0;top:0" width="1200" height="500" aria-hidden="true">
    <path d="M260 0 C420 60 700 20 900 0Z" fill="#65795a"/>
    <circle cx="1110" cy="30" r="60" fill="#6a7f60"/>
    <path d="M1100 500 C1060 380 1120 280 1200 250 L1200 500Z" fill="#6a7f60"/>
    <path d="M1090 40 C1150 70 1160 120 1200 170" stroke="#7d9073" fill="none"/>
  </svg>
  <div class="video" style="left:110px;top:63px;background:linear-gradient(160deg,#8a8d8c,#d8dad8 55%,#f0f0ee)" role="img" aria-label="Video still: hand wiping a boat console with a yellow microfiber towel">
    <div class="play"><svg width="16" height="16" viewBox="0 0 16 16"><path d="M5 3l8 5-8 5z" fill="#fff"/></svg></div>
  </div>
  <h2 class="product-title" style="left:600px;top:163px">WATERLESS WASH &amp; WAX</h2>
  <a class="btn btn-white" style="left:608px;top:250px;width:159px;height:54px">ADD TO CART</a>
</section>

<!-- Product: Graphene Ceramic Spray -->
<section class="abs band band-dark" style="top:1559px">
  <svg class="abs" style="left:0;top:0" width="1200" height="500" aria-hidden="true">
    <path d="M0 0 C60 30 90 80 60 120 C30 160 0 130 0 110Z" fill="#1e1e1e"/>
    <path d="M0 380 C150 330 380 360 560 500 L0 500Z" fill="#1c1c1c"/>
    <path d="M900 0 C1000 120 1120 140 1200 120 L1200 0Z" fill="#1b1b1b"/>
  </svg>
  <h2 class="product-title" style="left:110px;top:126px">GRAPHENE CERAMIC SPRAY<br>COATING AND PROTECTANT</h2>
  <a class="btn btn-green" style="left:114px;top:250px;width:158px;height:54px">ADD TO CART</a>
  <div class="video" style="left:658px;top:63px;background:linear-gradient(140deg,#f4f4f4,#cfd3d6 55%,#6b6f66)" role="img" aria-label="Video still: gloved hand holding a ceramic spray bottle against a boat hull">
    <div class="play"><svg width="16" height="16" viewBox="0 0 16 16"><path d="M5 3l8 5-8 5z" fill="#fff"/></svg></div>
  </div>
</section>

<!-- Product: Pink Soap -->
<section class="abs band band-green" style="top:2059px">
  <svg class="abs" style="left:0;top:0" width="1200" height="500" aria-hidden="true">
    <path d="M1200 0 C1080 90 1110 240 1200 300Z" fill="#65795a"/>
    <path d="M0 400 C140 420 260 470 300 500 L0 500Z" fill="#65795a"/>
  </svg>
  <div class="video" style="left:110px;top:63px;background:linear-gradient(100deg,#d8c87c,#e8dfb0 45%,#f3f1ea 60%,#cfbd6c)" role="img" aria-label="Video still: soap foam spread across a yellow boat hull">
    <div class="play"><svg width="16" height="16" viewBox="0 0 16 16"><path d="M5 3l8 5-8 5z" fill="#fff"/></svg></div>
  </div>
  <h2 class="product-title" style="left:605px;top:163px">PINK SOAP FOR BOATS</h2>
  <a class="btn btn-white" style="left:608px;top:248px;width:159px;height:54px">ADD TO CART</a>
</section>

<!-- Solution -->
<section>
  <h2 class="abs section-title" style="top:2630px;font-size:35px">THE VPX61 SOLUTION</h2>
  <p class="abs section-title" style="top:2696px;font-size:18px">CLEANING PRODUCTS THAT WORK THE FIRST TIME!</p>
  <article class="card" style="left:117px;top:2776px">
    <h3>WHAT’S THE BEST BOAT WAX?</h3>
    <p>We feel that a well-formulated, properly applied sprayable ceramic protectant is the easiest and most cost-effective way to protect and maintain the beauty of your boat's paint or gel coat. &nbsp;VPX61 Graphene Spray Protectant will provide up to one year of protection in favorable conditions and is easier than applying wax or sealers. &nbsp;This product can be used in direct sunlight on a hot surface and layered without issues.</p>
  </article>
  <article class="card" style="left:349px;top:3086px">
    <h3>WHY USE A WATERLESS WASH &amp; WAX?</h3>
    <p>Convenience! Waterless wash and wax products are the "new wave" of fast detailers because it offers more options in a single bottle. &nbsp;They may be used to clean light dirt, dust, and pollen from your watercraft. Cleaning solutions offer a scratch-free finish that can be used to wash and add extra protection with a synthetic wax barrier. &nbsp;A quick wipe with a high-quality microfiber towel is all that is needed.</p>
  </article>
  <a class="btn btn-green" style="left:461px;top:3402px;width:279px;height:54px">READ OUR BLOG FOR MORE</a>
</section>

<!-- Newsletter -->
<section class="abs newsletter">
  <h2 class="abs section-title" style="top:58px;font-size:35px;line-height:44px">JOIN OUR COMMUNITY: EXCLUSIVE DEALS, TIPS, AND<br>UPDATES STRAIGHT TO YOUR INBOX</h2>
  <p class="abs section-title" style="top:186px;font-family:'Lato',sans-serif;font-weight:400;font-size:15px;line-height:27px;color:var(--body)">Join today &amp; stay up-to-date on new product releases, shop promotions, and our<br>archery newsletters</p>
  <a class="btn btn-green" style="left:461px;top:269px;width:279px;height:54px">EMAIL FORM SUBMISSION</a>
</section>

<!-- Footer -->
<footer class="abs footer">
  <div class="abs logo">VPX61</div>
  <span class="social" style="left:169px"></span>
  <span class="social" style="left:206px"></span>
  <span class="social" style="left:242px"></span>
  <span class="social" style="left:278px"></span>
  <div class="fcol" style="left:439px">
    <h4>QUICK LINK</h4>
    <ul><li>Programs</li><li>Events</li><li>Online Store</li><li>About Us</li><li>Contact Us</li></ul>
  </div>
  <div class="fcol" style="left:622px">
    <h4>OTHER &nbsp;LINKS</h4>
    <ul><li>Case Studies</li><li>Miscellaneous information</li><li>Flagship</li><li>Terms of Service</li><li>Privacy Policy</li></ul>
  </div>
  <div class="fcol contact" style="left:864px">
    <h4>CONTACT INFORMATION</h4>
    <ul>
      <li><svg width="14" height="16" viewBox="0 0 14 16"><path d="M7 1a5 5 0 0 0-5 5c0 4 5 9 5 9s5-5 5-9a5 5 0 0 0-5-5z" fill="#fff"/><circle cx="7" cy="6" r="2" fill="#050505"/></svg><span>12b &nbsp;VPX61 Lorem<br>ipsum dolor sit amet</span></li>
      <li><svg width="14" height="12" viewBox="0 0 14 12"><rect x="0" y="1" width="14" height="10" fill="#fff"/><path d="M0 1l7 5 7-5" stroke="#050505" fill="none"/></svg><span>info@vpx61.com</span></li>
      <li><svg width="14" height="14" viewBox="0 0 14 14"><path d="M3 1l2.5 3-1.5 1.5a8 8 0 0 0 4.5 4.5L10 8.5l3 2.5-1.5 2.5C6 13 1 8 0.5 2.5z" fill="#fff"/></svg><span>+1 888 888 8888</span></li>
    </ul>
  </div>
  <div class="abs rule"></div>
  <p class="abs copy">©Copyrights 2023 VPX61 &nbsp;&nbsp;| &nbsp;&nbsp;All Rights Reserved</p>
</footer>

</body>
</html>
```